Q7 Landing Page

We are looking for a creative landing page & a autosignature for our email.
The launchpage will be featuring a dripmeadow provided "widget"
All instructions are in the uploaded ZIP File
**Please note that we require the landing page back complete ready to be uploaded without having to do any modifications**
Reason: Awaiting some further submissions...

```html
<!DOCTYPE html>
<html lang="en">
<head>
<meta charset="utf-8">
<title>Q7-MEDIA – Mobile Solutions</title>
<link rel="stylesheet" href="https://fonts.googleapis.com/css2?family=Ubuntu:wght@300;400;500;700&family=Comfortaa:wght@300;400&display=swap">
<style>
:root{
  --outer:#161616;
  --page:#2a2a2a;
  --page-dark:#232323;
  --green:#3aa335;
  --green-dark:#1f7a1f;
  --green-light:#7fbf3a;
  --hero-bg:#eef6f6;
  --white:#ffffff;
  --soft-white:#e6e6e6;
  --rule:#4a4a4a;
  --gold:#e8c23a;
  --badge:#f2d21f;
}
*{margin:0;padding:0;box-sizing:border-box}
html,body{width:1200px;height:1071px;overflow:hidden;background:var(--outer)}
body{font-family:"Ubuntu",sans-serif;color:var(--white);position:relative}
.page{position:absolute;left:69px;top:0;width:1097px;height:1071px;
  background:linear-gradient(90deg,var(--page-dark) 0%,var(--page) 20%,#2f2f2f 50%,var(--page) 80%,var(--page-dark) 100%)}
.abs{position:absolute}

/* header */
.brand-mark{left:244px;top:14px;width:50px;height:60px;background:var(--green);border-radius:4px}
.brand-name{left:195px;top:96px;font-weight:700;font-size:28px;letter-spacing:-0.5px;color:var(--white)}
.phone{left:771px;top:88px;display:flex;align-items:center;gap:10px;color:#b5b5b5;font-family:"Comfortaa",sans-serif;font-size:20px;font-style:italic}

/* hero */
.hero{left:180px;top:166px;width:840px;height:294px;background:var(--hero-bg);overflow:hidden}
.hero-title{left:34px;top:46px;font-weight:300;font-size:31px;line-height:30px;color:var(--green-light)}
.hero-title strong{font-weight:400;color:var(--green-dark);display:block}
.hero-sub{left:37px;top:120px;font-weight:300;font-size:26px;color:#8c8c8c}
.hero-list{left:37px;top:158px;list-style:none;font-weight:300;font-size:15.5px;line-height:18.5px;color:#9a9a9a}
.hero-list li::before{content:"-";margin-right:12px}
.hero-cta{left:34px;top:239px;font-size:16.5px;color:var(--green-dark)}
.btn{left:360px;top:224px;width:98px;height:31px;border-radius:16px;background:linear-gradient(#fafafa,#e2e2e2);
  border:1px solid #c9c9c9;box-shadow:0 0 0 3px #e9eded;font-size:11px;color:#555;display:flex;align-items:center;justify-content:center}
.hero-devices{left:493px;top:14px;width:296px;height:262px;border-radius:14px;
  background:linear-gradient(90deg,#2a2a2a 0%,#111 35%,#e07a3a 55%,#111 65%,#cfd3d4 85%,#9aa0a2 100%)}
.ribbon{right:0;top:0;width:100px;height:100px}

/* welcome */
.welcome{left:214px;top:512px;font-family:"Comfortaa",sans-serif;font-weight:300;font-size:28px;color:#cfcfcf}
.welcome span{font-family:"Ubuntu",sans-serif;font-weight:400;color:var(--white)}
.intro{left:214px;top:584px;width:462px;font-size:12.4px;line-height:14.5px;color:var(--soft-white)}
.intro p{margin-bottom:14px}

.apps-title{left:728px;top:516px;font-size:17px;font-weight:500}
.thumb{width:121px;height:92px;border:3px solid var(--white);box-shadow:0 0 0 1px #111}
.t1{left:728px;top:557px;background:linear-gradient(90deg,#e8e4dc 0 45%,#111 45% 50%,#8a4a2a 50%)}
.t2{left:866px;top:557px;background:linear-gradient(90deg,#5d6a5e 0 45%,#111 45% 50%,#68776a 50%)}
.t3{left:728px;top:670px;background:linear-gradient(90deg,#d8ccaa 0 45%,#111 45% 50%,#e0d6b8 50%)}
.t4{left:866px;top:670px;background:linear-gradient(90deg,#4b5a70 0 45%,#111 45% 50%,#b5371a 50%)}

/* testimonial */
.quote-band{left:216px;top:799px;width:770px;height:74px;background:linear-gradient(90deg,#5d5d5d,#6e6e6e 60%,#666)}
.quote-mark{left:32px;top:2px;font-family:"Ubuntu",sans-serif;font-weight:700;font-size:96px;line-height:96px;color:var(--white)}
.quote-text{left:97px;top:11px;width:470px;font-weight:300;font-size:12.5px;line-height:14.5px}
.quote-name{left:97px;top:52px;font-size:12px;color:var(--green)}
.badge{left:894px;top:788px;width:92px;height:92px;border-radius:50%;background:var(--badge);box-shadow:0 2px 6px rgba(0,0,0,.5)}

.rule{left:214px;width:772px;height:1px;background:var(--rule)}
.foot-h{top:925px;font-size:14.5px;font-weight:400}
.icons{left:215px;top:956px;display:flex;gap:7px}
.icons span{width:20px;height:20px;border-radius:3px;background:#5b7fa6}
.search{left:453px;top:956px;width:160px;height:23px;background:var(--white);border:1px solid #ccc;font-size:10px;font-style:italic;color:#aaa;padding:5px 8px}
.search-btn{left:620px;top:956px;width:37px;height:23px;border-radius:4px;background:linear-gradient(#4fa7ea,#1f6fc0);display:flex;align-items:center;justify-content:center}
.contact{left:730px;top:956px;font-size:12.5px;line-height:14.5px}
.copy{left:216px;top:1045px;font-size:10px}
</style>
</head>
<body>
<div class="page"></div>

<header>
  <div class="abs brand-mark"></div>
  <div class="abs brand-name">Q7-MEDIA</div>
  <div class="abs phone">
    <svg width="18" height="24" viewBox="0 0 18 24"><path d="M5 1 L2 3 Q0 12 7 22 L10 23 L12 20 L9 16 L7 17 Q4 12 5 7 L7 6 L7 1 Z" fill="#b5b5b5"/></svg>
    <span>1480 555 0192</span>
  </div>
</header>

<section class="abs hero">
  <h1 class="abs hero-title">Transferring the Web into your<strong>Pocket</strong></h1>
  <div class="abs hero-sub">Instant Apps for:</div>
  <ul class="abs hero-list"><li>Industries</li><li>Product Launches</li><li>Viral Marketing Campaigns.</li></ul>
  <div class="abs hero-cta">For Mobile Solutions, Come Talk to Us !</div>
  <div class="abs btn">Get Solution</div>
  <div class="abs hero-devices" role="img" aria-label="Three smartphones showing mobile apps"></div>
  <svg class="abs ribbon" viewBox="0 0 100 100"><polygon points="8,0 50,0 100,50 100,92" fill="var(--gold)"/><text x="68" y="36" transform="rotate(45 68 36)" font-family="Ubuntu,sans-serif" font-size="13" fill="#6b5410" text-anchor="middle">Join Us !</text></svg>
</section>

<main>
  <h2 class="abs welcome">Welcome <span>Q7-MEDIA</span></h2>
  <div class="abs intro">
    <p>Lorem Ipsum est simplement du faux texte employé dans la composition et la mise en page avant impression. Le Lorem Ipsum est le faux texte standard de l'imprimerie depuis les années 1500. Q</p>
    <p>uand un peintre anonyme assembla ensemble des morceaux de texte pour réaliser un livre spécimen de polices de texte. Il n'a pas fait que survivre cinq siècles, mais s'est aussi adapté à la bureautique informatique, sans que son.</p>
    <p>Contenu n'en soit modifié. Il a été popularisé dans les années 1960 grâce à la vente de feuilles Fernprint contenant des passages du Lorem Ipsum, et, plus récemment, par son inclusion dans des applications de mise en page de texte, comme Quillset Layout.</p>
  </div>

  <h3 class="abs apps-title">Latest Apps</h3>
  <div class="abs thumb t1" role="img" aria-label="Tablet app screenshot with bird and portrait artwork"></div>
  <div class="abs thumb t2" role="img" aria-label="Tablet app screenshot with green dashboard"></div>
  <div class="abs thumb t3" role="img" aria-label="Tablet app screenshot with world maps"></div>
  <div class="abs thumb t4" role="img" aria-label="Tablet app screenshot about volcanoes"></div>

  <section class="abs quote-band">
    <div class="abs quote-mark">“</div>
    <p class="abs quote-text">Great looking site! We are really happy with the way we work with Dorian, it's a real pleasure doing business in such professional and in the same time friendly manner.</p>
    <div class="abs quote-name">Lena Hartley</div>
  </section>
  <div class="abs badge" role="img" aria-label="Supported platforms badge"></div>
</main>

<footer>
  <div class="abs rule" style="top:904px"></div>
  <h4 class="abs foot-h" style="left:215px">Follow Us</h4>
  <h4 class="abs foot-h" style="left:452px">Newsletter</h4>
  <h4 class="abs foot-h" style="left:728px">Contact Us</h4>
  <div class="abs icons" aria-label="Social links"><span></span><span></span><span></span><span></span><span></span><span></span></div>
  <div class="abs search">Search the web</div>
  <div class="abs search-btn"><svg width="16" height="16" viewBox="0 0 16 16"><circle cx="10" cy="6" r="4.5" fill="none" stroke="#fff" stroke-width="2"/><line x1="7" y1="9" x2="2" y2="14" stroke="#fff" stroke-width="2.5"/></svg></div>
  <div class="abs contact">Web : www.q7-media.com<br>Email : hello@q7-media.com<br>Fax : 555-0148-227<br>Address : 48 Harbour Row, Suite 12, Westport</div>
  <div class="abs rule" style="top:1033px"></div>
  <div class="abs copy">© Copyrights 2012 All rights Reserved Privacy &amp; Legal</div>
</footer>
</body>
</html>
```